Construction business card

I need a new business card, they can connect with my logo, brand.
What we do is residential house , design and build
I like: Navy blue / black
I attached our logo, brand,
and, some idea for business card.

```html
<!DOCTYPE html>
<html lang="en">
<head>
<meta charset="utf-8">
<title>Harlow Building Group – Business Card</title>
<link rel="stylesheet" href="https://fonts.googleapis.com/css2?family=Archivo:wght@400;700;800&display=swap">
<style>
  :root {
    --stage: #1b1b1b;
    --card: #262626;
    --card-front: #242424;
    --emboss: #1a1a1a;
    --blue: #3a86d4;
    --white: #ffffff;
    --muted: #e6e6e6;
  }
  * { box-sizing: border-box; margin: 0; padding: 0; }
  html, body {
    width: 1200px; height: 900px; overflow: hidden;
    background: var(--stage);
    font-family: "Archivo", Arial, sans-serif;
  }
  .stage {
    position: relative; width: 1200px; height: 900px;
    display: flex; flex-direction: column; align-items: center; justify-content: center; gap: 48px;
  }
  .card {
    position: relative; width: 640px; height: 366px;
    border-radius: 22px; background: var(--card);
    box-shadow: 0 14px 30px rgba(0,0,0,.45);
    overflow: hidden;
  }
  .card--front { background: var(--card-front); }
  .brand-mark {
    display: flex; align-items: center; gap: 12px;
    font-weight: 800; text-transform: uppercase; letter-spacing: .04em; line-height: 1;
  }
  .brand-mark__square { width: 18px; height: 18px; background: currentColor; }
  .card--front .brand-mark {
    position: absolute; left: 50%; top: 50%; transform: translate(-50%, -50%);
    color: var(--emboss); font-size: 34px; white-space: nowrap;
  }
  .card--back .brand-mark {
    position: absolute; left: 50%; top: 58px; transform: translateX(-50%);
    color: var(--white); font-size: 24px; white-space: nowrap;
  }
  .brand-mark__square--accent { background: var(--blue); width: 14px; height: 14px; }
  .accent-line { position: absolute; inset: 0; }
  .holder {
    position: absolute; left: 50%; top: 112px; transform: translateX(-50%);
    text-align: center; line-height: 1.2; white-space: nowrap;
  }
  .holder__name { color: var(--blue); font-weight: 700; font-size: 26px; letter-spacing: .03em; }
  .holder__role { color: var(--muted); font-size: 15px; margin-top: 2px; }
  .address {
    position: absolute; right: 38px; top: 152px; text-align: right;
    color: var(--muted); font-size: 14px; line-height: 1.45; font-style: normal;
  }
  .contacts {
    position: absolute; left: 36px; bottom: 28px;
    list-style: none; color: var(--muted); font-size: 14px; line-height: 1.2;
  }
  .contacts li { display: flex; align-items: center; gap: 9px; margin-top: 6px; }
  .contacts svg { width: 14px; height: 14px; flex: none; }
</style>
</head>
<body>
<main class="stage">
  <section class="card card--front" aria-label="Card front">
    <div class="brand-mark"><span class="brand-mark__square"></span>Harlow Building Group</div>
  </section>

  <section class="card card--back" aria-label="Card back">
    <svg class="accent-line" width="640" height="366" viewBox="0 0 640 366" aria-hidden="true">
      <line x1="36" y1="255" x2="604" y2="105" stroke="var(--blue)" stroke-width="1.2"/>
    </svg>
    <div class="brand-mark"><span class="brand-mark__square brand-mark__square--accent"></span>Harlow Building Group</div>
    <div class="holder">
      <div class="holder__name">DANIEL REEVE</div>
      <div class="holder__role">CEO/Founder</div>
    </div>
    <address class="address">42 Ferncourt Rd<br>Glen Mara, VIC 3199</address>
    <ul class="contacts">
      <li>
        <svg viewBox="0 0 16 16" aria-hidden="true"><path fill="var(--blue)" d="M3.5 1.5l2.3 0 1 3.3-1.6 1.2a8 8 0 0 0 4.8 4.8l1.2-1.6 3.3 1v2.3c0 .8-.7 1.5-1.5 1.5A12.5 12.5 0 0 1 2 3c0-.8.7-1.5 1.5-1.5z"/></svg>
        0400 555 018
      </li>
      <li>
        <svg viewBox="0 0 16 16" aria-hidden="true"><rect x="1" y="3" width="14" height="10" rx="1.5" fill="var(--blue)"/><path d="M1.8 4l6.2 5 6.2-5" fill="none" stroke="var(--card)" stroke-width="1.3"/></svg>
        info@harlowbuilding.com.au
      </li>
      <li>
        <svg viewBox="0 0 16 16" aria-hidden="true"><circle cx="8" cy="8" r="7" fill="var(--blue)"/><path d="M1 8h14M8 1c-3 3.5-3 10.5 0 14M8 1c3 3.5 3 10.5 0 14" fill="none" stroke="var(--card)" stroke-width="1"/></svg>
        harlowbuilding.com.au
      </li>
    </ul>
  </section>
</main>
</body>
</html>
```